Create modern and sleek business card for luxury real estate company

We're a "boutique" real estate office looking for a design that gets across a highly modern luxury brand. Blacks and whites are probably the best colors unless we try a silver foil for the logo. I've attached a version of our current logo here. I'd like to swap out the current font on there with Gotham Light Regular.

I'm looking to have one side of the card have the logo with the space for our agents info on the other side.

Target Market(s)

Young professionals in a "luxury" headspace

Industry/Entity Type

Real estate

Contact Information for Business Card

A place for agent name, cell number, website. The slogan "Quietly Redefining Fine Homes".

Font styles to use
Other font styles liked:
• Gotham Regular

Colors

Designer to choose only greyscale colors for use in the design.

Requirements
Must have
• Matte black as the background color. Clean lines and use of contrast. A specific design aspect that will use silver foil.
Nice to have
• Up in the air on integrating a QR code
Should not have
• Any houses or other real estate related design (ex: a clip art house)

```html
<!DOCTYPE html>
<html lang="en">
<head>
<meta charset="utf-8">
<title>Northlane Realty — Business Card</title>
<link href="https://fonts.googleapis.com/css2?family=Montserrat:wght@300;400;600&display=swap" rel="stylesheet">
<style>
  :root {
    --backdrop: #2b2b2b;
    --card: #1d1d1d;
    --card-edge: #262626;
    --silver: #e4e4e4;
    --silver-soft: #bdbdbd;
    --muted: #9a9a9a;
    --gloss: #2a2a2a;
  }
  * { margin: 0; padding: 0; box-sizing: border-box; }
  html, body {
    width: 1200px; height: 900px; overflow: hidden;
    background: var(--backdrop);
    font-family: "Montserrat", sans-serif;
  }
  .sheet {
    width: 1200px; height: 900px;
    display: flex; flex-direction: column;
    align-items: center; justify-content: center; gap: 48px;
  }
  .card {
    position: relative;
    width: 700px; height: 400px;
    background: var(--card);
    border: 1px solid var(--card-edge);
    border-radius: 30px;
    overflow: hidden;
  }
  /* Front: brand side */
  .front {
    display: flex; flex-direction: column;
    align-items: center; justify-content: center; gap: 28px;
  }
  .brand { display: flex; align-items: center; gap: 22px; }
  .brand-mark {
    width: 86px; height: 86px; border-radius: 50%;
    border: 3px solid var(--silver);
    flex: none;
  }
  .brand-name {
    color: var(--silver);
    font-weight: 300; font-size: 48px; line-height: 1.05;
    letter-spacing: 3px; text-transform: uppercase;
  }
  .slogan {
    color: var(--silver);
    font-weight: 300; font-size: 20px;
    letter-spacing: 2px; text-transform: uppercase;
  }
  /* Back: agent side */
  .back { padding: 46px 50px; }
  .back .brand { gap: 12px; }
  .back .brand-mark { width: 40px; height: 40px; border-width: 2px; }
  .back .brand-name { font-size: 21px; letter-spacing: 1.5px; }
  .agent { margin-top: 40px; }
  .agent-name {
    color: var(--silver); font-weight: 600; font-size: 22px;
    letter-spacing: 1px; text-transform: uppercase;
  }
  .agent-role { color: var(--muted); font-weight: 400; font-size: 15px; margin-top: 4px; }
  .contacts { position: absolute; left: 50px; bottom: 46px; list-style: none; }
  .contacts li {
    display: flex; align-items: center; gap: 10px;
    color: var(--silver-soft); font-weight: 400; font-size: 16px; line-height: 28px;
  }
  .contacts svg { width: 14px; height: 14px; fill: none; stroke: var(--silver-soft); stroke-width: 2; }
  .seal {
    position: absolute; right: 60px; top: 70px;
    width: 260px; height: 260px; border-radius: 50%;
    border: 6px solid var(--gloss);
    box-shadow: 0 0 0 1px #333 inset, 0 0 0 1px #151515;
  }
</style>
</head>
<body>
<main class="sheet">
  <section class="card front">
    <div class="brand">
      <span class="brand-mark"></span>
      <span class="brand-name">Northlane<br>Realty</span>
    </div>
    <p class="slogan">Quietly Redefining Fine Homes</p>
  </section>

  <section class="card back">
    <div class="brand">
      <span class="brand-mark"></span>
      <span class="brand-name">Northlane<br>Realty</span>
    </div>
    <div class="agent">
      <p class="agent-name">Daniel Reyes</p>
      <p class="agent-role">Director</p>
    </div>
    <ul class="contacts">
      <li><svg viewBox="0 0 16 16"><path d="M4 2l2.5 3-1.5 2a8 8 0 0 0 4 4l2-1.5 3 2.5-1.5 2C7 14 2 9 2 3.5z"/></svg>555.014.2290</li>
      <li><svg viewBox="0 0 16 16"><rect x="2" y="4" width="12" height="9"/><path d="M2 4l6 5 6-5"/></svg>hello@northlanerealty.com</li>
      <li><svg viewBox="0 0 16 16"><circle cx="8" cy="8" r="6"/><path d="M2 8h12M8 2c3 3 3 9 0 12M8 2c-3 3-3 9 0 12"/></svg>www.northlanerealty.com</li>
    </ul>
    <span class="seal"></span>
  </section>
</main>
</body>
</html>
```